Classy, Elegant, Simple Business Card Design

Looking to have a classy, simple, and elegant design. Want a top notch designed business card. I really like the look of the new torvane credit card. I also like the design I attached. I am trying to reach 21-29 year old females for booking us for there wedding or event. We offer Disc Jockey Service, Photo Booth Rentals, and Uplighting .

Target Market(s)

21-28 year old females

Contact Information for Business Card

Has to have logo, website, email, and phone number

Font styles to use
Other font styles liked:
• open to font choice, modern, clean
Designer to choose
33a6d7
0791cd
0555a3
ffffff

Requirements
Must have
• Has to have logo, website, email, and phone number
Nice to have
• I really like the design of the new torvane credit card. I also included my logo and some designs I like
Should not have
• clutter or too much info

```html
<!DOCTYPE html>
<html lang="en">
<head>
<meta charset="UTF-8">
<title>Velvet Echo Event Group – Business Card</title>
<link href="https://fonts.googleapis.com/css2?family=Roboto:wght@400;500;700&display=swap" rel="stylesheet">
<style>
  :root {
    --backdrop: #3a3a3a;
    --card: #232323;
    --card-edge: #1a1a1a;
    --ink: #ffffff;
    --ink-soft: #d8d8d8;
    --gloss: #6f6f6f;
    --sky: #33a6d7;
    --blue: #0791cd;
    --deep: #0555a3;
    --rule: #4a4a4a;
  }
  * { margin: 0; padding: 0; box-sizing: border-box; }
  html, body {
    width: 799px; height: 1200px; overflow: hidden;
    background: var(--backdrop);
    font-family: "Roboto", Arial, sans-serif;
  }
  .canvas {
    width: 799px; height: 1200px;
    display: flex; flex-direction: column; align-items: center; justify-content: space-around;
    padding: 60px 0;
  }
  .card {
    position: relative;
    width: 620px; height: 354px;
    background: var(--card);
    border: 1px solid var(--card-edge);
    box-shadow: 0 18px 40px rgba(0,0,0,.45);
    overflow: hidden;
  }
  /* Front */
  .card--front { display: flex; align-items: center; justify-content: center; gap: 16px; }
  .brand-dot {
    width: 22px; height: 22px; border-radius: 50%;
    background: var(--gloss);
  }
  .brand-name {
    font-weight: 500; font-size: 44px; letter-spacing: 4px;
    color: var(--gloss); text-transform: uppercase;
  }
  /* Back */
  .card--back { display: flex; }
  .back-left {
    width: 52%; position: relative;
    display: flex; flex-direction: column; align-items: center; justify-content: center;
  }
  .back-left .brand {
    display: flex; align-items: center; gap: 10px; margin-top: -40px;
  }
  .back-left .brand-dot { width: 14px; height: 14px; background: var(--blue); }
  .back-left .brand-name { font-size: 27px; letter-spacing: 2px; color: var(--blue); }
  .services {
    position: absolute; left: 34px; bottom: 34px;
    font-size: 15px; color: var(--ink); white-space: nowrap;
  }
  .services .sep { color: var(--blue); margin: 0 10px; }
  .divider {
    width: 1px; background: var(--rule);
    margin: 70px 0 80px;
  }
  .back-right {
    flex: 1; padding: 88px 0 0 36px; color: var(--ink);
  }
  .person-name { font-size: 27px; font-weight: 700; color: var(--blue); }
  .person-title { font-size: 15px; margin-top: 2px; color: var(--ink-soft); }
  .contacts { list-style: none; margin-top: 30px; }
  .contacts li {
    display: flex; align-items: center; gap: 12px;
    font-size: 15px; margin-bottom: 9px;
  }
  .contacts svg { width: 15px; height: 15px; flex: none; }
</style>
</head>
<body>
  <main class="canvas">
    <section class="card card--front" aria-label="Card front">
      <span class="brand-dot"></span>
      <span class="brand-name">Velvet Echo</span>
    </section>

    <section class="card card--back" aria-label="Card back">
      <div class="back-left">
        <div class="brand">
          <span class="brand-dot"></span>
          <span class="brand-name">Velvet Echo</span>
        </div>
        <p class="services">Disc Jockeys<span class="sep">/</span>Photo Booths<span class="sep">/</span>And More..</p>
      </div>
      <div class="divider"></div>
      <div class="back-right">
        <h1 class="person-name">Marcus Hale</h1>
        <p class="person-title">Founder &amp; CEO</p>
        <ul class="contacts">
          <li>
            <svg viewBox="0 0 16 16" aria-hidden="true"><path fill="var(--blue)" d="M2 3h12v3h-3V5H5v1H2zM4 7h8l2 6H2z"/></svg>
            555 0142 0142
          </li>
          <li>
            <svg viewBox="0 0 16 16" aria-hidden="true"><rect x="1" y="3" width="14" height="10" fill="var(--blue)"/><path d="M1 3l7 6 7-6" stroke="var(--card)" stroke-width="1.4" fill="none"/></svg>
            marcus@velvetecho.com
          </li>
          <li>
            <svg viewBox="0 0 16 16" aria-hidden="true"><circle cx="8" cy="8" r="6.5" fill="none" stroke="var(--blue)" stroke-width="1.5"/><ellipse cx="8" cy="8" rx="2.8" ry="6.5" fill="none" stroke="var(--blue)" stroke-width="1.2"/><path d="M1.5 8h13" stroke="var(--blue)" stroke-width="1.2"/></svg>
            www.velvetecho.com
          </li>
        </ul>
      </div>
    </section>
  </main>
</body>
</html>
```